We are a recruitment company based in Norwich/Cambridge England.
I have included our company logo which we want to remain the same.

What we are looking for is a new creative Business card which will really stand out!!

Contact Information for Business Card

Harriet Dunmore
email: Harriet@plavex.co.uk
Address: Brackwell House
Fenmoor Enterprise Park
Partridge Way
Norwich
QB9 3KX
Tel:01632 960418

```html
<!DOCTYPE html>
<html lang="en">
<head>
<meta charset="utf-8">
<title>Plavex Business Card</title>
<link rel="stylesheet" href="https://fonts.googleapis.com/css2?family=Montserrat:wght@400;500;700&display=swap">
<style>
  :root {
    --backdrop: #2f2a28;
    --card-white: #ffffff;
    --card-grey: #87848a;
    --brand-green: #7cc142;
    --ink-grey: #6d6d72;
    --ink-dark: #2b2b2b;
    --tag-grey: #a9a9ad;
    --on-grey: #ffffff;
  }
  html, body {
    margin: 0;
    padding: 0;
    width: 1200px;
    height: 844px;
    overflow: hidden;
    background: var(--backdrop);
    font-family: "Montserrat", sans-serif;
  }
  .stage {
    position: relative;
    width: 1200px;
    height: 844px;
  }
  .card {
    position: absolute;
    top: 267px;
    width: 540px;
    height: 310px;
    box-sizing: border-box;
    box-shadow: 0 10px 30px rgba(0, 0, 0, 0.45);
  }
  .card--front {
    left: 45px;
    background: var(--card-white);
  }
  .card--back {
    left: 615px;
    background: var(--card-grey);
  }

  /* Brand lockup */
  .brand {
    position: absolute;
    display: flex;
    align-items: center;
    gap: 12px;
  }
  .brand__dot {
    width: 34px;
    height: 34px;
    border-radius: 50%;
    flex: none;
  }
  .brand__text {
    display: flex;
    flex-direction: column;
  }
  .brand__name {
    font-weight: 500;
    font-size: 38px;
    line-height: 1;
    letter-spacing: -0.5px;
  }
  .brand__tagline {
    font-size: 8.5px;
    letter-spacing: 2.6px;
    margin-top: 4px;
  }
  .card--front .brand {
    top: 34px;
    right: 34px;
  }
  .card--front .brand__dot { background: var(--brand-green); }
  .card--front .brand__name { color: var(--brand-green); }
  .card--front .brand__tagline { color: var(--tag-grey); }

  .card--back .brand {
    top: 112px;
    left: 50%;
    transform: translateX(-50%);
  }
  .card--back .brand__dot { background: var(--on-grey); width: 42px; height: 42px; }
  .card--back .brand__name { color: var(--on-grey); font-size: 44px; }
  .card--back .brand__tagline { color: var(--on-grey); }

  .web-address {
    position: absolute;
    top: 196px;
    left: 0;
    right: 0;
    text-align: center;
    color: var(--on-grey);
    font-size: 11px;
    letter-spacing: 0.3px;
  }

  /* Contact block */
  .person {
    position: absolute;
    left: 34px;
    top: 150px;
  }
  .person__name {
    margin: 0;
    font-weight: 700;
    font-size: 19px;
    letter-spacing: 0.4px;
    text-transform: uppercase;
    color: var(--ink-grey);
  }
  .person__name .first { color: var(--brand-green); }
  .person__role {
    margin: 1px 0 10px;
    font-size: 12.5px;
    color: var(--ink-dark);
  }
  .contact-list {
    list-style: none;
    margin: 0;
    padding: 0;
  }
  .contact-list li {
    display: flex;
    align-items: center;
    gap: 10px;
    font-size: 13px;
    line-height: 21px;
    color: var(--ink-dark);
  }
  .contact-list svg {
    width: 11px;
    height: 11px;
    fill: var(--brand-green);
    flex: none;
  }
  .contact-list .no-icon { padding-left: 21px; }
</style>
</head>
<body>
<main class="stage">

  <section class="card card--front" aria-label="Card front">
    <div class="brand">
      <span class="brand__dot"></span>
      <div class="brand__text">
        <span class="brand__name">Plavex</span>
        <span class="brand__tagline">Technology Recruitment</span>
      </div>
    </div>

    <div class="person">
      <h1 class="person__name"><span class="first">Harriet</span> Dunmore</h1>
      <p class="person__role">Managing Director</p>
      <ul class="contact-list">
        <li>
          <svg viewBox="0 0 12 12" aria-hidden="true"><path d="M2.5 1 4.5 1 5.3 3.6 4 4.6C4.7 6 6 7.3 7.4 8L8.4 6.7 11 7.5 11 9.5C11 10.3 10.3 11 9.5 11 5 11 1 7 1 2.5 1 1.7 1.7 1 2.5 1Z"/></svg>
          01632 960418
        </li>
        <li>
          <svg viewBox="0 0 12 12" aria-hidden="true"><path d="M6 0.5C3.8 0.5 2.2 2.2 2.2 4.3 2.2 7.2 6 11.5 6 11.5S9.8 7.2 9.8 4.3C9.8 2.2 8.2 0.5 6 0.5ZM6 5.8A1.5 1.5 0 1 1 6 2.8 1.5 1.5 0 0 1 6 5.8Z"/></svg>
          Brackwell House, Fenmoor Enterprise Park
        </li>
        <li class="no-icon">Partridge Way, Norwich QB9 3KX</li>
        <li>
          <svg viewBox="0 0 12 12" aria-hidden="true"><path d="M0.5 2.5H11.5V9.5H0.5ZM1.3 3.2 6 6.6 10.7 3.2"/></svg>
          Harriet@plavex.co.uk
        </li>
      </ul>
    </div>
  </section>

  <section class="card card--back" aria-label="Card back">
    <div class="brand">
      <span class="brand__dot"></span>
      <div class="brand__text">
        <span class="brand__name">Plavex</span>
        <span class="brand__tagline">Technology Recruitment</span>
      </div>
    </div>
    <p class="web-address">www.plavex.co.uk</p>
  </section>

</main>
</body>
</html>
```